Website Design Request - Management Consulting Firm

We need a Website designed for an IT Management Staffing and Recruiting firm called TRAVENOK based in San Francisco.

The firm is an high-end technology staffing agency. Our focus is on quality and high-caliber candidates rather than quantity.

The website will have two main home pages. One for the recruiter and another on for the candidates.

The website needs to optimize for mobile devices as well.

I have attached few mock-ups that I have done just to show what I am thinking. The UI needs to be very clean, fluid, and it needs to have a modern, rustic, professional feel to it.

Target Market(s)

Technology Manager, Director, VP, CIO of Companies that have $4b-10b dollar revenue. Such as larkspurdwellings.example , https://www.velmorian.example/, quillnet.example, zib.example

Industry/Entity Type

Management Consulting

Number of Pages Required

5+ page

Font styles to use
Sans Serif

Colors
f37122
ffffff

Requirements
Must have
• Please review mock-ups for suggestions
Nice to have
Should not have

```html
<!DOCTYPE html>
<html lang="en">
<head>
<meta charset="utf-8">
<title>TRAVENOK – IT Project Management Jobs</title>
<link href="https://fonts.googleapis.com/css2?family=Nunito+Sans:wght@400;600;700&display=swap" rel="stylesheet">
<style>
:root{
  --orange:#f37122;
  --white:#ffffff;
  --ink:#2b2b2b;
  --muted:#444;
  --footer:#f2f2f2;
  --bar:#e4e4e4;
  --teal:#95d3cb;
  --line:#888;
}
*{box-sizing:border-box;margin:0;padding:0}
html,body{width:824px;height:1200px;overflow:hidden;background:var(--white)}
body{position:relative;font-family:"Nunito Sans",Arial,sans-serif;color:var(--ink)}
.abs{position:absolute}
.brand{left:111px;top:10px;color:var(--orange);font-size:31px;font-weight:700;letter-spacing:1px;line-height:32px}
.brand-tag{left:111px;top:43px;font-size:7px;letter-spacing:.8px;color:#333}
.nav a{position:absolute;top:28px;font-size:8.5px;color:#222;text-decoration:none}
.signup{left:662px;top:23px;width:46px;height:23px;border:1px solid var(--orange);color:var(--orange);font-size:8.5px;display:flex;align-items:center;justify-content:center}
.hero{left:0;top:70px;width:824px;height:373px;background:linear-gradient(180deg,#e9e6e2 0%,#d7d2cc 45%,#6d7784 75%,#4a4f5a 100%)}
.hero-panel{left:221px;top:222px;width:382px;height:128px;background:rgba(255,255,255,.88)}
.hero-title{left:221px;width:382px;top:241px;text-align:center;color:var(--orange);font-size:14.5px;font-weight:600}
.hero-sub{left:221px;width:382px;top:264px;text-align:center;font-size:8.5px;font-weight:600}
.email{left:263px;top:286px;width:210px;height:23px;border:1px solid var(--orange);background:var(--white);font-size:6.5px;color:#999;padding:7px 8px}
.offers{left:478px;top:286px;width:83px;height:23px;background:var(--orange);color:var(--white);font-size:8.5px;font-weight:700;display:flex;align-items:center;justify-content:center}
.talent{left:221px;width:382px;top:324px;text-align:center;font-size:8px;font-weight:600}
.talent span{color:var(--orange);font-weight:400;margin-left:8px}
.dot{top:410px;width:7px;height:7px;border-radius:50%;background:var(--white)}
.tab-on{left:0;top:443px;width:412px;height:42px;background:var(--orange);color:var(--white);font-size:14px;font-weight:600;text-align:center;padding:11px 0 0 240px}
.tab-off{left:443px;top:454px;color:var(--orange);font-size:14px;font-weight:600}
.h2{left:0;width:824px;top:508px;text-align:center;color:var(--orange);font-size:14px;font-weight:600}
.lead{left:0;width:824px;top:549px;text-align:center;font-size:9.5px;font-weight:600}
.step-title{font-size:9.5px;font-weight:600}
.step-desc{font-size:6.5px;line-height:8px}
.num{font-size:13px;font-weight:600}
.circle{border-radius:50%}
.cta{left:318px;top:936px;width:188px;height:34px;background:var(--orange);color:var(--white);font-size:13.5px;font-weight:600;display:flex;align-items:center;justify-content:center;gap:14px}
.footer{left:0;top:1008px;width:824px;height:166px;background:var(--footer)}
.f-head{top:1034px;font-size:9.5px;font-weight:600}
.links li{list-style:none;position:absolute;left:0;font-size:7.5px;font-weight:600;white-space:nowrap}
.links li::before{content:"›";position:absolute;left:-10px;top:-2px;font-size:10px}
.nl-input{left:266px;top:1057px;width:115px;height:17px;background:var(--white);border:1px solid #ddd;font-size:6px;font-weight:600;padding:4px 6px}
.subscribe{left:267px;top:1078px;width:57px;height:16px;background:var(--orange);color:var(--white);font-size:6.5px;font-weight:600;display:flex;align-items:center;justify-content:center}
.social{top:1106px;width:24px;height:24px;border:1px solid #ddd;background:#f7f7f7}
.social.on{background:var(--orange);border-color:var(--orange)}
.contact{font-size:6.5px;color:#333;left:454px}
.map{left:554px;top:1043px;width:144px;height:104px;background:linear-gradient(135deg,#cfe3f0,#e8e4d8 50%,#b8d4e8);border:1px solid #ccc}
.bottom{left:0;top:1174px;width:824px;height:26px;background:var(--bar);font-size:7px;text-align:center;padding-top:8px}
</style>
</head>
<body>
<header>
  <div class="abs brand">TRAVENOK</div>
  <div class="abs brand-tag">PROJECT MANAGEMENT CONSULTING</div>
  <nav class="nav">
    <a style="left:500px">Professionals</a>
    <a style="left:568px">Employers</a>
    <a style="left:626px">Sign in</a>
  </nav>
  <div class="abs signup">Sign Up</div>
</header>

<section>
  <div class="abs hero" role="img" aria-label="Photo of six smiling business professionals seated in a row against a white brick wall"></div>
  <div class="abs hero-panel"></div>
  <h1 class="abs hero-title">Looking For IT Project Management Jobs?</h1>
  <p class="abs hero-sub">Upload your resume, accept interview requests, get offers</p>
  <div class="abs email">Enter email id
    <svg style="position:absolute;right:7px;top:6px" width="9" height="9" viewBox="0 0 10 10"><path d="M1 4 L5 1 L9 4 V9 H1 Z M1 4 L5 7 L9 4" fill="none" stroke="#777" stroke-width=".9"/></svg>
  </div>
  <div class="abs offers">Get Offers Now</div>
  <p class="abs talent">Looking for Talents ?<span>See how it works for Employers</span></p>
  <div class="abs dot" style="left:395px"></div>
  <div class="abs dot" style="left:408px;background:var(--orange)"></div>
  <div class="abs dot" style="left:421px"></div>
</section>

<section>
  <div class="abs tab-on">How it works ?</div>
  <svg class="abs" style="left:368px;top:484px" width="16" height="8"><path d="M0 0 H16 L8 8 Z" fill="#f37122"/></svg>
  <div class="abs tab-off">Why Us ?</div>

  <h2 class="abs h2">3 Simple Steps</h2>
  <p class="abs lead">Employers pay 25% more for a better FIT Project Manager</p>

  <svg class="abs" style="left:406px;top:578px" width="12" height="356">
    <line x1="6" y1="4" x2="6" y2="356" stroke="#888" stroke-width="1" stroke-dasharray="2 2"/>
    <circle cx="6" cy="4" r="3.5" fill="#f37122"/>
    <circle cx="6" cy="119" r="3.5" fill="#f37122"/>
    <circle cx="6" cy="233" r="3.5" fill="#f37122"/>
  </svg>
  <div class="abs num" style="left:418px;top:582px">01</div>
  <div class="abs num" style="left:390px;top:695px">02</div>
  <div class="abs num" style="left:421px;top:809px">03</div>

  <div class="abs step-title" style="left:207px;top:599px">Upload your resume</div>
  <div class="abs step-desc" style="left:207px;top:617px">Answer few questions and upload your resume</div>
  <div class="abs circle" style="left:500px;top:574px;width:104px;height:104px;background:var(--teal)" role="img" aria-label="Illustration of a resume being reviewed under a magnifying glass"></div>

  <div class="abs circle" style="left:220px;top:666px;width:104px;height:104px;background:var(--teal)" role="img" aria-label="Illustration of two people meeting across a desk for an interview"></div>
  <div class="abs step-title" style="left:474px;top:702px">We send you interview requests</div>
  <div class="abs step-desc" style="left:474px;top:719px;width:160px">Interested in someone? With a single click, send interview request and let us handle the rest</div>

  <div class="abs step-title" style="left:206px;top:811px">Get $1000 Bonus</div>
  <div class="abs step-desc" style="left:206px;top:830px">Find a job and get $1000 bonus TRAVENOK</div>
  <div class="abs circle" style="left:500px;top:782px;width:104px;height:104px;background:var(--teal)" role="img" aria-label="Illustration of a light bulb formed by puzzle pieces"></div>

  <div class="abs cta">
    <svg width="16" height="14" viewBox="0 0 16 14"><path d="M8 0 L13 5 H10 V9 H6 V5 H3 Z" fill="#fff"/><path d="M1 9 V13 H15 V9" fill="none" stroke="#fff" stroke-width="2"/></svg>
    Upload your resume
  </div>
</section>

<footer>
  <div class="abs footer"></div>
  <div class="abs f-head" style="left:122px">Quick Links</div>
  <ul class="abs links" style="left:135px;top:1062px">
    <li style="top:0">Home</li>
    <li style="top:19px">Professionals</li>
    <li style="top:37px">Employers</li>
    <li style="top:56px">Sign in</li>
    <li style="top:74px">Sign up</li>
  </ul>

  <div class="abs f-head" style="left:267px">Newsletter</div>
  <div class="abs nl-input">Enter Email id</div>
  <div class="abs subscribe">Subscribe</div>
  <div class="abs social on" style="left:268px"></div>
  <div class="abs social" style="left:299px"></div>
  <div class="abs social" style="left:331px"></div>
  <div class="abs social" style="left:363px"></div>

  <div class="abs f-head" style="left:436px">Contact Us</div>
  <svg class="abs" style="left:437px;top:1055px" width="8" height="8" viewBox="0 0 10 10"><path d="M2 1 L4 3 L3 4.5 Q4.5 6.5 5.5 7 L7 6 L9 8 L7.5 9.5 Q2 8 0.5 2.5 Z" fill="#333"/></svg>
  <div class="abs contact" style="top:1055px">Phone : 1-800 555 0147</div>
  <svg class="abs" style="left:436px;top:1074px" width="9" height="7" viewBox="0 0 10 8"><rect x=".5" y=".5" width="9" height="7" fill="none" stroke="#333"/><path d="M.5 .5 L5 4.5 L9.5 .5" fill="none" stroke="#333"/></svg>
  <div class="abs contact" style="top:1073px">Email : info@travenok.example</div>
  <svg class="abs" style="left:437px;top:1100px" width="8" height="10" viewBox="0 0 8 10"><path d="M4 10 L1 5 A3.5 3.5 0 1 1 7 5 Z" fill="#333"/><circle cx="4" cy="3.6" r="1.3" fill="#f2f2f2"/></svg>
  <div class="abs contact" style="top:1101px">Address : Travenok</div>
  <div class="abs contact" style="top:1119px">Level 23, 5 Orrin Street</div>
  <div class="abs contact" style="top:1137px">Maribel NSW 2000</div>
  <div class="abs map" role="img" aria-label="Street map showing the office location"></div>

  <div class="abs bottom">© 2016. www.travenok.example</div>
</footer>
</body>
</html>
```